Business card por a urban DJ, up scale audience target

Need a sober design, modern, conservative colors but i can consider some options, y play rnb, hip hop, EDM and top40.

Business card for contact and personal info, double sided, use logo attrached please; im 42 so i need a card acording to my age an target audience.

Target Market(s)

Adult people, up scale audience

Industry/Entity Type

Music Download

Contact Information for Business Card

Cel (318) 4207265518 www.lumadrift.com

Requirements
Must have
• open mind
Nice to have
• open mind
Should not have
• DJ

```html
<!DOCTYPE html>
<html lang="en">
<head>
<meta charset="utf-8">
<title>Lumadrift Business Card</title>
<link href="https://fonts.googleapis.com/css2?family=Jost:wght@400;500;700&display=swap" rel="stylesheet">
<style>
  :root {
    --backdrop: #3b3e43;
    --card-light: #fbfbfb;
    --card-dark: #151515;
    --ink: #141414;
    --paper: #ffffff;
  }
  * { margin: 0; padding: 0; box-sizing: border-box; }
  html, body {
    width: 1200px; height: 750px; overflow: hidden;
    background: var(--backdrop);
    font-family: "Jost", sans-serif;
  }
  .stage { position: relative; width: 1200px; height: 750px; }
  .card {
    position: absolute; top: 228px; width: 462px; height: 263px; overflow: hidden;
  }
  .card--front { left: 124px; background: var(--card-light); }
  .card--back { left: 618px; background: var(--card-dark); color: var(--paper); }

  .brand-name {
    position: absolute; right: 48px; top: 134px; transform: translateY(-50%);
    font-weight: 700; font-size: 72px; letter-spacing: 1px; line-height: 1;
    color: var(--ink); white-space: nowrap;
  }
  .edge-bar {
    position: absolute; top: 86px; width: 11px; height: 97px;
  }
  .card--front .edge-bar { right: 0; background: var(--ink); }
  .card--back .edge-bar { left: 0; background: var(--paper); }

  .contact { position: absolute; left: 31px; top: 91px; }
  .contact__name { font-size: 18px; font-weight: 500; letter-spacing: 0.3px; line-height: 1.1; }
  .contact__role { font-size: 13.5px; font-weight: 500; margin-top: 4px; }
  .contact__list { list-style: none; margin-top: 16px; font-size: 13px; font-weight: 400; }
  .contact__list li { display: flex; align-items: center; gap: 7px; height: 18px; }
  .contact__list svg { width: 11px; height: 12px; flex: none; }
</style>
</head>
<body>
<main class="stage">
  <section class="card card--front" aria-label="Card front">
    <div class="brand-name">LUMA</div>
    <span class="edge-bar"></span>
  </section>

  <section class="card card--back" aria-label="Card back">
    <span class="edge-bar"></span>
    <div class="contact">
      <h1 class="contact__name">ANDRE COLE</h1>
      <p class="contact__role">CEO/FOUNDER</p>
      <ul class="contact__list">
        <li>
          <svg viewBox="0 0 11 12" aria-hidden="true"><rect x="2" y="0.5" width="7" height="11" rx="1" fill="none" stroke="#fff" stroke-width="1.2"/><rect x="4" y="9" width="3" height="1" fill="#fff"/></svg>
          (318) 4207265518
        </li>
        <li>
          <svg viewBox="0 0 12 12" aria-hidden="true"><circle cx="6" cy="6" r="5.5" fill="#fff"/><path d="M3 3.5 Q5 4 4.5 6 Q6 7 5 9.5 M8 2.5 Q7 4.5 9 5 Q10 7 8.5 9" stroke="#151515" stroke-width="1.1" fill="none"/></svg>
          www.lumadrift.com
        </li>
      </ul>
    </div>
  </section>
</main>
</body>
</html>
```